flat authentication

design an authentication plate and an authentication certificate

on both you need the Brix vintage store logo
authentication plate size 10 * 7cm
color black transparent text
aluminum plate material
American vintage spirit in the years 1950 to 1960

an authentication certificate
page size 4
the text to put above is in the word file
color black white red blue golden
on the certificate I would like the round golden pastille (like a seal)

```html
<!DOCTYPE html>
<html lang="en">
<head>
<meta charset="utf-8">
<title>Authentication Plate – Brix vintage store</title>
<link rel="stylesheet" href="https://fonts.googleapis.com/css2?family=UnifrakturMaguntia&family=Open+Sans:wght@700&display=swap">
<style>
  :root {
    --plate-black: #000000;
    --field-white: #ffffff;
    --alu-light: #f2f4f5;
    --alu-mid: #c9cdd0;
    --alu-dark: #9ea4a8;
    --label-white: #ffffff;
  }
  html, body {
    margin: 0;
    padding: 0;
    width: 1200px;
    height: 840px;
    overflow: hidden;
    background: #ffffff;
  }
  .plate {
    display: block;
    width: 1200px;
    height: 840px;
  }
  .plate-title {
    font-family: "UnifrakturMaguntia", serif;
    font-size: 112px;
    fill: var(--label-white);
  }
  .field-label {
    font-family: "Open Sans", sans-serif;
    font-weight: 700;
    font-size: 33px;
    fill: var(--label-white);
  }
  .footer-line {
    font-family: "Open Sans", sans-serif;
    font-weight: 700;
    font-size: 34px;
    fill: var(--label-white);
  }
  .store-name {
    font-family: "Open Sans", sans-serif;
    font-weight: 700;
    fill: var(--label-white);
  }
  .store-name-main { font-size: 36px; }
  .store-name-sub { font-size: 24px; }
  .star { fill: var(--label-white); }
  .entry-field { fill: var(--field-white); }
  .mount-hole { fill: var(--field-white); stroke: var(--alu-mid); stroke-width: 2; }
  .panel { fill: var(--plate-black); }
  .store-disc { fill: var(--plate-black); stroke: var(--alu-light); stroke-width: 6; }
</style>
</head>
<body>
<svg class="plate" viewBox="0 0 1200 840" xmlns="http://www.w3.org/2000/svg" role="img" aria-label="Aluminium authentication plate for Brix vintage store">
  <defs>
    <linearGradient id="brushed-aluminium" x1="0" y1="0" x2="1" y2="1">
      <stop offset="0" stop-color="var(--alu-light)"/>
      <stop offset="0.35" stop-color="var(--alu-mid)"/>
      <stop offset="0.55" stop-color="var(--alu-light)"/>
      <stop offset="0.8" stop-color="var(--alu-dark)"/>
      <stop offset="1" stop-color="var(--alu-mid)"/>
    </linearGradient>
    <path id="title-arc" d="M95,185 Q592,58 1092,195"/>
    <path id="star-shape" d="M0,-22 L5.2,-7.1 L20.9,-6.8 L8.4,2.7 L12.9,17.8 L0,8.8 L-12.9,17.8 L-8.4,2.7 L-20.9,-6.8 L-5.2,-7.1 Z"/>
  </defs>

  <rect class="plate-base" x="0" y="0" width="1184" height="827" rx="44" fill="url(#brushed-aluminium)"/>

  <rect class="panel panel-top" x="18" y="18" width="1148" height="260" rx="38"/>
  <rect class="panel panel-bottom" x="18" y="292" width="1148" height="517" rx="38"/>

  <circle class="mount-hole" cx="55" cy="48" r="19"/>
  <circle class="mount-hole" cx="1127" cy="48" r="19"/>
  <circle class="mount-hole" cx="55" cy="766" r="19"/>
  <circle class="mount-hole" cx="1127" cy="766" r="19"/>

  <text class="plate-title"><textPath href="#title-arc" startOffset="50%" text-anchor="middle" textLength="990" lengthAdjust="spacing">Authentication Plate</textPath></text>

  <g class="stars">
    <use class="star" href="#star-shape" transform="translate(122,242) scale(0.85)"/>
    <use class="star" href="#star-shape" transform="translate(194,242) scale(0.9)"/>
    <use class="star" href="#star-shape" transform="translate(272,240) scale(1)"/>
    <use class="star" href="#star-shape" transform="translate(358,238) scale(1.1)"/>
    <use class="star" href="#star-shape" transform="translate(824,238) scale(1.1)"/>
    <use class="star" href="#star-shape" transform="translate(908,240) scale(1)"/>
    <use class="star" href="#star-shape" transform="translate(988,242) scale(0.9)"/>
    <use class="star" href="#star-shape" transform="translate(1058,242) scale(0.85)"/>
  </g>

  <g class="store-mark">
    <circle class="store-disc" cx="592" cy="262" r="118"/>
    <text class="store-name store-name-main" x="592" y="258" text-anchor="middle">Brix</text>
    <text class="store-name store-name-sub" x="592" y="292" text-anchor="middle">vintage store</text>
  </g>

  <text class="field-label" x="243" y="354" text-anchor="middle">Product</text>
  <rect class="entry-field" x="38" y="365" width="431" height="104" rx="11"/>

  <text class="field-label" x="925" y="354" text-anchor="middle">Origin of the product</text>
  <rect class="entry-field" x="710" y="365" width="431" height="104" rx="11"/>

  <text class="field-label" x="230" y="517" text-anchor="middle">Restoration</text>
  <text class="field-label" x="230" y="554" text-anchor="middle">Number</text>
  <rect class="entry-field" x="143" y="567" width="163" height="92" rx="7"/>

  <text class="field-label" x="593" y="554" text-anchor="middle">Model</text>
  <rect class="entry-field" x="513" y="567" width="163" height="92" rx="7"/>

  <text class="field-label" x="970" y="554" text-anchor="middle">Year</text>
  <rect class="entry-field" x="897" y="567" width="163" height="92" rx="7"/>

  <text class="footer-line" x="118" y="753">Restored in Belgium by our craftsman</text>
  <rect class="entry-field" x="806" y="677" width="255" height="100" rx="9"/>
</svg>
</body>
</html>
```